SkyvornQ Business Cards and Stationary Design

Need a design for our business cards and stationary. I want to carry on the theme of the logo. I want the business cards to have a design on the back. I would like the business cards and the stationary to carry the same theme, design scheme, and branding

Target Market(s)

Airlines and Maintenance Facilities

Industry/Entity Type

Aviation

Contact Information for Business Card

Name
Position Title
Address: 4827 Trellis Hollow Road, Marrowind, Calvera, 34951
Office Number
Mobile Number
Email
Website

Font styles to use
Serif
Sans Serif

Colors

Designer to choose colors to be used in the design.

```html
<!DOCTYPE html>
<html lang="en">
<head>
<meta charset="utf-8">
<title>SkyvornQ Business Card</title>
<link rel="stylesheet" href="https://fonts.googleapis.com/css2?family=Montserrat:wght@500;700;800&family=Quicksand:wght@500;600&display=swap">
<style>
  :root {
    --navy: #1f2d52;
    --navy-deep: #1a2a4f;
    --navy-soft: #2c3f6e;
    --blue: #1a5a9c;
    --sky: #2a9bd8;
    --ink: #4a4a4a;
    --white: #ffffff;
    --paper: #ececec;
    --rule: #b8b8b8;
  }
  * { margin: 0; padding: 0; box-sizing: border-box; }
  html, body { width: 1200px; height: 960px; overflow: hidden; background: var(--paper); }
  body { position: relative; font-family: "Quicksand", sans-serif; }

  .card {
    position: absolute;
    left: 220px;
    width: 760px;
    height: 434px;
    overflow: hidden;
    box-shadow: 0 6px 18px rgba(0,0,0,.15);
  }

  /* Back side */
  .card-back { top: 30px; background: var(--navy); color: var(--white); }
  .back-brand {
    position: absolute; left: 0; right: 0; top: 150px;
    display: flex; flex-direction: column; align-items: center; gap: 22px;
  }
  .brand-dot {
    width: 74px; height: 74px; border-radius: 50%;
    border: 8px solid var(--white);
  }
  .back-name {
    font-family: "Montserrat", sans-serif; font-weight: 800;
    font-size: 54px; letter-spacing: 9px; color: var(--white);
  }
  .back-web {
    position: absolute; left: 0; right: 0; bottom: 40px; text-align: center;
    font-family: "Montserrat", sans-serif; font-weight: 500; font-size: 19px; letter-spacing: 1px;
  }

  /* Front side */
  .card-front { top: 496px; background: var(--white); }
  .front-brand {
    position: absolute; left: 70px; top: 70px; width: 300px;
    display: flex; flex-direction: column; align-items: center; gap: 16px;
  }
  .front-brand .brand-dot { width: 96px; height: 96px; border: 8px solid var(--blue); }
  .front-name {
    font-family: "Montserrat", sans-serif; font-weight: 800;
    font-size: 38px; letter-spacing: 6px; color: var(--navy-deep);
  }
  .divider {
    position: absolute; left: 400px; top: 60px; width: 1px; height: 200px; background: var(--rule);
  }
  .contact { position: absolute; left: 438px; top: 56px; color: var(--ink); }
  .person {
    font-family: "Montserrat", sans-serif; font-weight: 700; font-size: 27px; color: #555;
  }
  .role { font-size: 17px; margin-top: 2px; }
  .address { font-size: 17px; line-height: 1.35; margin-top: 16px; }
  .lines { list-style: none; margin-top: 14px; font-size: 18px; }
  .lines li { display: flex; align-items: center; gap: 12px; line-height: 1.5; }
  .lines svg { width: 18px; height: 18px; flex: none; }
  .wave { position: absolute; left: 0; bottom: 0; width: 760px; height: 160px; }
  .front-web {
    position: absolute; left: 60px; bottom: 30px; color: var(--white);
    font-family: "Montserrat", sans-serif; font-weight: 500; font-size: 19px; letter-spacing: .5px;
  }
</style>
</head>
<body>
  <section class="card card-back">
    <div class="back-brand">
      <div class="brand-dot"></div>
      <div class="back-name">SKYVORNQ</div>
    </div>
    <div class="back-web">www.skyvornq.com</div>
  </section>

  <section class="card card-front">
    <div class="front-brand">
      <div class="brand-dot"></div>
      <div class="front-name">SKYVORNQ</div>
    </div>
    <div class="divider"></div>
    <div class="contact">
      <div class="person">Dorian PELL</div>
      <div class="role">CEO / Founder</div>
      <div class="address">4827 Trellis Hollow Road<br>Marrowind, Calvera, 34951</div>
      <ul class="lines">
        <li><svg viewBox="0 0 24 24" fill="none" stroke="#2a9bd8" stroke-width="2.2"><path d="M5 3h4l2 5-3 2a12 12 0 0 0 6 6l2-3 5 2v4a2 2 0 0 1-2 2A18 18 0 0 1 3 5a2 2 0 0 1 2-2z"/></svg>000.000.0000</li>
        <li><svg viewBox="0 0 24 24" fill="none" stroke="#2a9bd8" stroke-width="2.2"><rect x="6" y="2" width="12" height="20" rx="2"/><line x1="11" y1="18" x2="13" y2="18"/></svg>000.000.0000</li>
        <li><svg viewBox="0 0 24 24" fill="none" stroke="#2a9bd8" stroke-width="2"><rect x="2" y="5" width="20" height="14"/><path d="M2 5l10 8 10-8"/></svg>dorian@skyvornq.com</li>
      </ul>
    </div>
    <svg class="wave" viewBox="0 0 760 160" preserveAspectRatio="none" aria-hidden="true">
      <path d="M420 112 C560 132 680 122 760 108 L760 160 L420 160Z" fill="var(--navy-soft)"/>
      <path d="M0 28 C160 0 320 20 460 85 C580 135 680 146 760 144 L760 160 L0 160Z" fill="var(--sky)"/>
      <path d="M0 34 C170 10 320 35 450 95 C570 145 680 152 760 151 L760 160 L0 160Z" fill="var(--blue)"/>
      <path d="M0 44 C170 25 310 55 430 110 C520 150 620 160 760 160 L0 160Z" fill="var(--navy-deep)"/>
    </svg>
    <div class="front-web">www.skyvornq.com</div>
  </section>
</body>
</html>
```